Homemaking training schools needs a Business Card design

Designer, Hello!

No special requirements, good-looking enough.
--------------------------------------------------------------------------

Name: Marcus Dole
Chairman
Tel: 0574-71948263
Mobile: 13857420916
Email: kelvora@mailnest.example
Web: www.prt2019.example
Add: No.258, LanpingJie, BeiyuanQu, Ningbo, Zhejiang

LOGO
Ningbo PRT Homemaking Training School

Target Market(s)

pregnant women, mothers, infants, the elderly and families, including cleaning, cooking, nursing training.

Industry/Entity Type

Business

Contact Information for Business Card

Name: Marcus Dole
Chairman
Tel: 0574-71948263
Mobile: 13857420916
Email: kelvora@mailnest.example
Web: www.prt2019.example

LOGO

Font styles to use
Serif
Sans Serif
Decorative

Requirements
Nice to have
• Feels: clean, specifications, safety, comfort, warmth and happiness.

```html
<!DOCTYPE html>
<html lang="en">
<head>
<meta charset="utf-8">
<title>PingRuiTang Business Card</title>
<link rel="stylesheet" href="https://fonts.googleapis.com/css2?family=Open+Sans:wght@400;600&display=swap">
<style>
  :root {
    --stage: #1b1b1b;
    --card-white: #ffffff;
    --brand-blue: #1565b0;
    --brand-pink: #e6007e;
  }
  html, body {
    margin: 0;
    width: 1200px;
    height: 900px;
    overflow: hidden;
    background: var(--stage);
    font-family: "Open Sans", Arial, sans-serif;
  }
  .card {
    position: absolute;
    top: 306px;
    width: 440px;
    height: 271px;
    border-radius: 12px;
    overflow: hidden;
  }
  .card-front { left: 149px; background: var(--card-white); }
  .card-back { left: 608px; background: var(--brand-pink); }

  .brand {
    position: absolute;
    left: 0;
    width: 100%;
    text-align: center;
    font-weight: 600;
    font-size: 30px;
    line-height: 40px;
    letter-spacing: -0.3px;
    white-space: nowrap;
    color: var(--brand-blue);
  }
  .card-front .brand { top: 76px; }
  .card-back .brand { top: 116px; }

  .holder {
    position: absolute;
    right: 220px;
    top: 162px;
    text-align: right;
    color: var(--brand-pink);
    font-size: 12px;
    line-height: 19px;
  }
  .holder-name {
    color: var(--brand-blue);
    font-weight: 600;
    font-size: 16px;
    line-height: 20px;
  }
  .holder-role { margin-bottom: 2px; }

  .contacts {
    position: absolute;
    left: 238px;
    top: 163px;
    margin: 0;
    padding: 0;
    list-style: none;
    color: var(--brand-pink);
    font-size: 12px;
    line-height: 18.5px;
  }
  .contacts li { display: flex; align-items: center; gap: 6px; white-space: nowrap; }
  .contacts svg { width: 9px; height: 9px; fill: var(--brand-blue); flex: none; }
</style>
</head>
<body>
  <section class="card card-front" aria-label="Card front">
    <div class="brand">PingRuiTang</div>

    <div class="holder">
      <div class="holder-name">Marcus Dole</div>
      <div class="holder-role">Chairman</div>
      <div class="holder-address">No.258, LanpingJie,<br>BeiyuanQu, Ningbo, Zhejiang</div>
    </div>

    <ul class="contacts">
      <li><svg viewBox="0 0 10 10"><path d="M2 0.5l2 2-1 1.2c.6 1.3 1.6 2.3 2.9 2.9l1.2-1 2 2-1.3 1.4C4.5 8.8 1.2 5.5.6 1.8z"/></svg>0574-71948263</li>
      <li><svg viewBox="0 0 10 10"><path d="M2.5 0h5v10h-5zM3.5 1.2v6.6h3V1.2z"/></svg>13857420916</li>
      <li><svg viewBox="0 0 10 10"><path d="M0 2h10v6H0z"/><path d="M0.8 2.6L5 5.6l4.2-3" fill="none" stroke="#fff" stroke-width="0.9"/></svg>kelvora@mailnest.example</li>
      <li><svg viewBox="0 0 10 10"><circle cx="5" cy="5" r="5"/></svg>www.prt2019.example</li>
    </ul>
  </section>

  <section class="card card-back" aria-label="Card back">
    <div class="brand">PingRuiTang</div>
  </section>
</body>
</html>
```